Mental Health care Company in Washington DC

We are a new mental health care services provider in Washington DC. Please look at these sites.
https://brightwaterfamilysupport.com
https://www.quietharborinc.com
https://willowgate-dc.org/
https://www.tidepathdc.com
https://www.thelanternofdc.com

```html
<!DOCTYPE html>
<html lang="en">
<head>
<meta charset="utf-8">
<title>Nova Health Services — Empowering Mental Wellness in DC</title>
<link href="https://fonts.googleapis.com/css2?family=Poppins:wght@300;400;500;600;700&family=Caveat:wght@500&display=swap" rel="stylesheet">
<style>
:root{
  --navy:#0f2447;
  --navy-2:#1c3557;
  --orange:#f28024;
  --orange-2:#f59a3c;
  --teal:#5cc3cb;
  --ink:#1a1f2b;
  --body:#4a4f5a;
  --line:#d9dde3;
  --pale:#eef6f8;
  --white:#ffffff;
}
*{margin:0;padding:0;box-sizing:border-box}
html,body{width:1200px;height:4071px;overflow:hidden}
body{font-family:'Poppins',sans-serif;color:var(--ink);background:var(--white);position:relative}
.abs{position:absolute}
a{color:inherit;text-decoration:none}
.btn{display:inline-block;background:var(--orange);color:#fff;font-weight:500;border-radius:30px;text-align:center}

/* top bar & header */
.topbar{left:0;top:0;width:1200px;height:29px;background:var(--navy);color:#fff;font-size:11px;text-align:center;line-height:29px;letter-spacing:.2px}
.header{left:0;top:29px;width:1200px;height:80px;background:#fff;border-bottom:4px solid #eef0f3}
.brand{left:141px;top:12px}
.brand-name{font-size:33px;font-weight:500;color:var(--navy);line-height:1}
.brand-sub{font-size:10px;letter-spacing:6px;color:var(--navy);text-align:center;margin-top:3px}
.nav{left:414px;top:28px;display:flex;gap:28px;font-size:13px;color:var(--ink)}
.nav-cta{left:864px;top:22px;width:196px;height:37px;line-height:37px;font-size:13px}

/* hero */
.hero{left:0;top:112px;width:1200px;height:552px;background:linear-gradient(90deg,#1d3a5f 0%,#3c6286 45%,#a9bfd0 75%,#dfe6ec 100%)}
.hero-title{left:141px;top:240px;font-size:48px;font-weight:600;color:#fff;line-height:56px}
.hero-title span{color:var(--teal)}
.hero-text{left:141px;top:372px;font-size:15px;color:#fff;line-height:27px}
.hero-btn{left:141px;top:459px;width:139px;height:36px;line-height:36px;font-size:13px}

/* features */
.feature{top:736px;width:300px}
.feature-icon{position:absolute;left:0;top:0;width:62px;height:62px;border-radius:50%;border:1px solid var(--line);display:flex;align-items:center;justify-content:center}
.feature h3{margin-left:83px;font-size:14px;font-weight:500;line-height:22px}
.feature p{margin-left:83px;margin-top:8px;font-size:11px;line-height:19px;color:var(--body)}
.divider{left:103px;top:886px;width:993px;height:1px;background:var(--line)}

/* question banner */
.ask{left:141px;top:957px;width:917px;height:209px;border-radius:18px;background:linear-gradient(90deg,#f07a1e 0%,#f59b4a 55%,#dfe9f0 80%,#e9eef3 100%)}
.ask-script{left:209px;top:995px;font-family:'Caveat',cursive;font-size:26px;color:#ffe3c4}
.ask-title{left:209px;top:1026px;font-size:22px;font-weight:500;color:#fff;line-height:34px}
.ask-link{left:209px;top:1104px;font-size:13px;color:#fff;text-decoration:underline}

/* marquee */
.marquee{left:0;top:1252px;width:1200px;height:49px;background:var(--teal);color:#fff;font-size:15px;display:flex;align-items:center;gap:16px;white-space:nowrap;overflow:hidden}
.marquee span{display:flex;align-items:center;gap:16px}

/* about */
.about-bg{left:0;top:1301px;width:605px;height:569px;background:var(--pale)}
.about-line{left:605px;top:1301px;width:1px;height:569px;background:var(--line)}
.about-rule{left:0;top:1869px;width:1200px;height:1px;background:var(--line)}
.about-photo{left:0;top:1387px;width:520px;height:397px;border-radius:0 14px 14px 0;background:linear-gradient(120deg,#9cb7cc,#3f8fc4 55%,#d7e4ee)}
.eyebrow{font-size:14px;color:var(--teal);letter-spacing:.3px}
.about-eyebrow{left:673px;top:1393px}
.about-title{left:673px;top:1426px;font-size:30px;font-weight:500;color:var(--navy);line-height:36px}
.about-text{left:673px;top:1512px;width:435px;font-size:12.3px;line-height:22.6px;color:var(--ink)}
.about-btn{left:673px;top:1745px;width:195px;height:35px;line-height:35px;font-size:12px}

/* services */
.svc-head{left:0;top:1958px;width:1200px;text-align:center}
.svc-title{left:0;top:2000px;width:1200px;text-align:center;font-size:29px;font-weight:500;color:var(--navy)}
.card{top:2077px;width:281px;height:318px;border:1.5px solid #9aa2ad;border-bottom:none;text-align:center}
.card::after{content:"";position:absolute;left:-1px;bottom:0;width:281px;height:1.5px;background:linear-gradient(90deg,#9aa2ad 0,#9aa2ad 36%,transparent 36%,transparent 64%,#9aa2ad 64%)}
.card-img{margin:14px 15px 0;height:140px;background:linear-gradient(135deg,#d9d2ca,#9fb2c6)}
.card h3{font-size:16px;font-weight:400;margin-top:22px}
.card p{font-size:12px;line-height:22px;color:var(--body);margin:12px 18px 0}
.card-badge{position:absolute;left:116px;bottom:-25px;width:50px;height:50px;border-radius:50%;background:var(--teal);display:flex;align-items:center;justify-content:center}

/* wellness cta */
.well{left:0;top:2514px;width:1200px;height:403px;background:linear-gradient(90deg,#e8ddd2 0%,#d9b48d 35%,#f28024 62%,#f28024 100%)}
.well-title{left:630px;top:2578px;font-size:32px;font-weight:500;color:#ffe6cc;line-height:48px}
.well-text{left:630px;top:2710px;font-size:13px;line-height:26px;color:#ffe6cc}
.well-btn{left:630px;top:2793px;width:247px;height:37px;line-height:35px;font-size:13px;background:transparent;border:1.5px solid #ffe6cc;color:#ffe6cc}

/* outline words */
.words{left:-8px;top:2974px;width:1216px;white-space:nowrap;font-size:66px;font-weight:700;letter-spacing:0;line-height:1;overflow:hidden}
.words .ol{color:transparent;-webkit-text-stroke:1.5px #9aa2ad}
.words .solid{color:var(--ink)}

/* testimonials */
.tst-title{left:0;top:3122px;width:1200px;text-align:center;font-size:31px;font-weight:500;line-height:42px}
.tcard{top:3250px;width:284px;height:220px;background:#fff;box-shadow:0 4px 18px rgba(20,30,50,.08);padding:16px 22px}
.tquote{position:absolute;right:-6px;top:-20px;width:38px;height:38px;border-radius:50%;background:#fff;border:2px solid var(--teal);color:var(--teal);font-size:26px;font-weight:700;text-align:center;line-height:40px}
.tquote.or{border-color:var(--orange);color:var(--orange)}
.tavatar{width:58px;height:58px;border-radius:50%;background:linear-gradient(135deg,#c9ced6,#6f7a88)}
.stars{position:absolute;left:100px;top:36px;color:var(--orange);font-size:17px;letter-spacing:2px}
.tname{font-size:13px;font-weight:500;margin-top:14px}
.ttext{font-size:11px;line-height:20px;color:var(--body);margin-top:4px}
.dots{left:557px;top:3514px;display:flex;gap:7px}
.dots i{width:11px;height:11px;border-radius:50%;background:#e3e5e9;display:block}
.dots i.on{background:var(--orange)}

/* footer */
.footer{left:0;top:3605px;width:1200px;height:466px;background:var(--navy);color:#fff}
.f-brand{left:139px;top:3710px}
.f-brand .brand-name,.f-brand .brand-sub{color:#fff}
.f-about,.f-links,.f-contact,.news-p,.f-copy,.f-legal{color:var(--white)}
.f-about{left:139px;top:3790px;width:200px;font-size:12px;line-height:22px}
.f-h{font-size:16px;font-weight:500;color:var(--orange)}
.f-links{left:368px;top:3714px}
.f-links ul{list-style:none;margin-top:14px;font-size:12px;line-height:32px}
.f-links li::before{content:"• "}
.f-contact{left:526px;top:3714px;font-size:12px;line-height:22px}
.f-contact .lbl{color:var(--orange);margin-top:14px}
.news{left:781px;top:3692px;width:291px;height:253px;background:var(--navy-2);border-radius:10px}
.news-h{left:818px;top:3714px}
.news-p{left:818px;top:3750px;font-size:12px;line-height:22px}
.news-in{left:818px;top:3820px;width:218px;height:36px;border-radius:20px;background:#fff;color:#8a919c;font-size:11px;line-height:36px;padding-left:20px}
.news-btn{left:818px;top:3875px;width:152px;height:36px;line-height:36px;font-size:13px}
.f-rule{left:139px;top:4014px;width:922px;height:1px;background:#34496a}
.f-copy{left:141px;top:4038px;font-size:12px}
.f-legal{left:757px;top:4038px;font-size:12px}
</style>
</head>
<body>

<div class="abs topbar">WELCOME TO NOVA HEALTH – EMPOWERING MENTAL WELLNESS IN DC</div>

<header class="abs header">
  <div class="abs brand"><div class="brand-name">Nova Health</div><div class="brand-sub">SERVICES</div></div>
  <nav class="abs nav"><a>Home</a><a>About Us ▾</a><a>Services ▾</a><a>Blog</a><a>FAQs</a><a>Contact</a></nav>
  <a class="abs btn nav-cta">Make an Appointment</a>
</header>

<section class="abs hero" role="img" aria-label="Photo of a smiling doctor in a white coat speaking with a patient"></section>
<h1 class="abs hero-title">Empowering Minds<span>.</span><br>Restoring Lives<span>.</span></h1>
<p class="abs hero-text">Compassionate, Client-Centered Mental Health Services<br>Tailored For Washington DC’s Diverse Communities.</p>
<a class="abs btn hero-btn">Get Started</a>

<div class="abs feature" style="left:141px">
  <div class="feature-icon"><svg width="30" height="30" viewBox="0 0 30 30" fill="none" stroke="#f28024" stroke-width="1.6"><path d="M4 20h6l6 3 10-6-2-2-7 3h-5"/><path d="M15 13c-3-2-5-4-5-6a2.5 2.5 0 015-1 2.5 2.5 0 015 1c0 2-2 4-5 6z"/></svg></div>
  <h3>Personalized Family Care</h3>
  <p>We treat you like family, building lasting relationships based on trust and compassion</p>
</div>
<div class="abs feature" style="left:451px">
  <div class="feature-icon"><svg width="30" height="30" viewBox="0 0 30 30" fill="none" stroke="#5cc3cb" stroke-width="1.6"><path d="M15 25C7 19 4 15 4 10a5 5 0 0111-2 5 5 0 0111 2c0 5-3 9-11 15z"/><path d="M15 11v7M11.5 14.5h7"/></svg></div>
  <h3>Comprehensive Services</h3>
  <p>From routine checkups to specialized testing, we offer a wide range of services to meet your needs</p>
</div>
<div class="abs feature" style="left:768px">
  <div class="feature-icon"><svg width="30" height="30" viewBox="0 0 30 30" fill="none" stroke="#f28024" stroke-width="1.6"><circle cx="15" cy="15" r="10"/><path d="M11 15h8M15 11v8"/></svg></div>
  <h3>Experienced &amp; Caring Staff</h3>
  <p>Our team of dedicated professionals is committed to providing the highest quality care</p>
</div>
<div class="abs divider"></div>

<section class="abs ask" role="img" aria-label="Doctor holding a stethoscope beside the appointment message"></section>
<div class="abs ask-script">Have A Question?</div>
<h2 class="abs ask-title">Reach out to schedule your appointment or<br>get answers to your questions</h2>
<a class="abs ask-link">Schedule an Appointment Today!</a>

<div class="abs marquee">
  <span style="margin-left:-12px">te Care</span>
  <span><svg width="20" height="18" viewBox="0 0 20 18" fill="none" stroke="#fff" stroke-width="1.5"><path d="M10 16C3 11 1.5 8 1.5 5.5a4 4 0 018.5-1.5 4 4 0 018.5 1.5C18.5 8 17 11 10 16z"/></svg>Family-Focused</span>
  <span><svg width="20" height="18" viewBox="0 0 20 18" fill="none" stroke="#fff" stroke-width="1.5"><path d="M10 16C3 11 1.5 8 1.5 5.5a4 4 0 018.5-1.5 4 4 0 018.5 1.5C18.5 8 17 11 10 16z"/></svg>Comprehensive Services</span>
  <span><svg width="20" height="18" viewBox="0 0 20 18" fill="none" stroke="#fff" stroke-width="1.5"><path d="M10 16C3 11 1.5 8 1.5 5.5a4 4 0 018.5-1.5 4 4 0 018.5 1.5C18.5 8 17 11 10 16z"/></svg>Advanced Testing</span>
  <span><svg width="20" height="18" viewBox="0 0 20 18" fill="none" stroke="#fff" stroke-width="1.5"><path d="M10 16C3 11 1.5 8 1.5 5.5a4 4 0 018.5-1.5 4 4 0 018.5 1.5C18.5 8 17 11 10 16z"/></svg>Community Health</span>
  <span><svg width="20" height="18" viewBox="0 0 20 18" fill="none" stroke="#fff" stroke-width="1.5"><path d="M10 16C3 11 1.5 8 1.5 5.5a4 4 0 018.5-1.5 4 4 0 018.5 1.5C18.5 8 17 11 10 16z"/></svg>Personalized Healthcare</span>
  <span><svg width="20" height="18" viewBox="0 0 20 18" fill="none" stroke="#fff" stroke-width="1.5"><path d="M10 16C3 11 1.5 8 1.5 5.5a4 4 0 018.5-1.5 4 4 0 018.5 1.5C18.5 8 17 11 10 16z"/></svg>Comp</span>
</div>

<div class="abs about-bg"></div>
<div class="abs about-line"></div>
<div class="abs about-rule"></div>
<div class="abs about-photo" role="img" aria-label="Father and son giving a high five to a smiling nurse"></div>
<div class="abs eyebrow about-eyebrow">WHO WE ARE <svg width="90" height="14" viewBox="0 0 90 14" style="vertical-align:middle"><path d="M9 1v12M3 7h12" stroke="#f28024" stroke-width="2"/><path d="M20 7h70" stroke="#d9dde3"/></svg></div>
<h2 class="abs about-title">A Trusted Mental Health<br>Partner In DC</h2>
<p class="abs about-text">Lorem Ipsum is simply dummy text of the printing and typesetting industry. Lorem Ipsum has been the industry's standard dummy text ever since the 1500s, when an unknown printer took a galley of type and scrambled it to make a type specimen book. It has survived not only five centuries, but also the leap into electronic typesetting, remaining essentially unchanged. It was popularised in the 1960s with the release of Letraset sheets containing Lorem Ipsum passages, and more recently with desktop publishing software like Aldus PageMaker including versions of Lorem Ipsum</p>
<a class="abs btn about-btn">Learn More About Us</a>

<div class="abs svc-head"><div class="eyebrow">OUR CORE SERVICES</div><svg width="80" height="14" viewBox="0 0 80 14"><path d="M0 7h32M48 7h32" stroke="#d9dde3"/><path d="M40 1v12M34 7h12" stroke="#f28024" stroke-width="2"/></svg></div>
<h2 class="abs svc-title">Transformative Services For Real Results</h2>

<div class="abs card" style="left:141px">
  <div class="card-img" role="img" aria-label="Therapist listening to a young woman on a sofa"></div>
  <h3>Individual Therapy</h3>
  <p>Lorem Ipsum is simply dummy text of the printing and typesetting industry. Lorem Ipsum has been the.</p>
  <div class="card-badge"><svg width="24" height="24" viewBox="0 0 24 24" fill="none" stroke="#fff" stroke-width="1.6"><circle cx="12" cy="10" r="7"/><path d="M12 17v5M9 10h6M12 7v6"/></svg></div>
</div>
<div class="abs card" style="left:459px">
  <div class="card-img" role="img" aria-label="Group of smiling medical staff standing together"></div>
  <h3>Support Groups</h3>
  <p>Lorem Ipsum is simply dummy text of the printing and typesetting industry. Lorem Ipsum has been the.</p>
  <div class="card-badge"><svg width="24" height="24" viewBox="0 0 24 24" fill="none" stroke="#fff" stroke-width="1.6"><circle cx="8" cy="8" r="3"/><circle cx="16" cy="8" r="3"/><circle cx="12" cy="15" r="3"/><path d="M3 20c1-3 3-4 5-4M21 20c-1-3-3-4-5-4"/></svg></div>
</div>
<div class="abs card" style="left:778px">
  <div class="card-img" role="img" aria-label="Clinician counseling an older patient at a desk"></div>
  <h3>Counseling</h3>
  <p>Lorem Ipsum is simply dummy text of the printing and typesetting industry. Lorem Ipsum has been the.</p>
  <div class="card-badge"><svg width="24" height="24" viewBox="0 0 24 24" fill="none" stroke="#fff" stroke-width="1.6"><rect x="3" y="4" width="18" height="13" rx="2"/><path d="M7 9h10M7 13h6M8 17l-2 4"/></svg></div>
</div>

<section class="abs well" role="img" aria-label="Smiling woman and clinician reviewing notes on a clipboard"></section>
<h2 class="abs well-title">Ready To Begin<br>Your Journey To Wellness?</h2>
<p class="abs well-text">Get started on the path to health through the quality<br>medical care our team provides!</p>
<a class="abs btn well-btn">Schedule Your Appointment</a>

<div class="abs words"><span class="ol">stworthy_</span> <span class="solid">Caring_</span> <span class="ol">Professional</span></div>

<h2 class="abs tst-title">What Our Clients Are Saying – Real Success Stories<br>from Trusted Partners</h2>

<div class="abs tcard" style="left:-158px"><div class="tquote">”</div><div class="tavatar" role="img" aria-label="Client portrait"></div><div class="stars">★★☆</div><div class="tname">&nbsp;</div><p class="ttext">dummy text of the industry. Lorem dustry's standard the 1500s, when an galley of type.</p></div>
<div class="abs tcard" style="left:150px"><div class="tquote or">”</div><div class="tavatar" role="img" aria-label="Client portrait"></div><div class="stars">★★★☆☆</div><div class="tname">Reid Calloway</div><p class="ttext">Lorem Ipsum is simply dummy text of the printing and typesetting industry. Lorem Ipsum has been the industry's standard dummy text ever since the 1500s.</p></div>
<div class="abs tcard" style="left:457px"><div class="tquote">”</div><div class="tavatar" role="img" aria-label="Client portrait"></div><div class="stars">★★★☆☆</div><div class="tname">Milo Fenwick</div><p class="ttext">Lorem Ipsum is simply dummy text of the printing and typesetting industry. Lorem Ipsum has been the industry's.</p></div>
<div class="abs tcard" style="left:765px"><div class="tquote or">”</div><div class="tavatar" role="img" aria-label="Client portrait"></div><div class="stars">★★★☆☆</div><div class="tname">Lena Ostrova</div><p class="ttext">Lorem Ipsum is simply dummy text of the printing and typesetting industry. Lorem Ipsum has been the industry's standard dummy text ever since the 1500s, when an unknown printer took a galley of type.</p></div>
<div class="abs tcard" style="left:1073px"><div class="tavatar" role="img" aria-label="Client portrait"></div><div class="stars">★</div><div class="tname">Carla Whitby</div><p class="ttext">Lorem Ipsum is sim printing and types Ipsum has been th dummy text ever.</p></div>
<div class="abs dots"><i class="on"></i><i></i><i></i><i></i><i></i></div>

<footer class="abs footer"></footer>
<div class="abs f-brand"><div class="brand-name">Nova Health</div><div class="brand-sub">SERVICES</div></div>
<p class="abs f-about">Committed to providing expert mental health care in Washington DC, we empower individuals to heal, grow, and thrive</p>
<div class="abs f-links"><div class="f-h">Quick Links</div><ul><li>Home</li><li>About Us</li><li>Sevices</li><li>Blog</li><li>FAQs</li><li>Contact Us</li></ul></div>
<div class="abs f-contact"><div class="f-h">Contact Info</div><p style="margin-top:14px">2210 Linden Row Suite 4, Marlow,<br>Vermont 05344, United States</p><p class="lbl">Email Address :</p><p>hello@novamentalhealth.com</p><p class="lbl">Phone Number :</p><p>(555)-201-4418</p></div>
<div class="abs news"></div>
<div class="abs f-h news-h">Stay in Touch</div>
<p class="abs news-p">Stay updated with health tips<br>and exclusive offers!</p>
<div class="abs news-in">Email address<svg style="position:absolute;right:18px;top:12px" width="16" height="12" viewBox="0 0 16 12" fill="none" stroke="#8a919c" stroke-width="1.4"><rect x="1" y="1" width="14" height="10" rx="1"/><path d="M1 2l7 5 7-5"/></svg></div>
<a class="abs btn news-btn">Subscribe&nbsp;&nbsp;&nbsp;<svg width="12" height="12" viewBox="0 0 12 12" style="vertical-align:-1px"><path d="M1 1l10 5-10 5 2-5z" fill="#fff"/></svg></a>
<div class="abs f-rule"></div>
<div class="abs f-copy">Copyright © 2025 Nova Mental Health | All Rights Reserved.</div>
<div class="abs f-legal">Terms &amp; Condition &nbsp;|&nbsp; Privacy Policy &nbsp;|&nbsp; Support</div>

</body>
</html>
```